Real estate business card

I need a business card for my real estate company. I help clients buy and sell properties. I would like to keep the design very simple and professional. I would like the design to convey professionalism, safety and trust. I prefer no graphics but a simple logo design would be nice if that is part of what you do.
Updates

Please keep the designs simple. No high-rise buildings please. 

Project Deadline Extended
Reason: My design has not been finalized.

Target Market(s)

Age group 30-60 mostly affluent

Industry/Entity Type

Real Estate

Contact Information for Business Card

Velmont Realtors
Gregory Velmont, Broker
4815 Brindle Ave. #263, La Crescenta, CA 91206

Requirements
Nice to have
• Logo can be combination of my initials GV or just Z or a simple geometric shape? Please see "Desig Ideas" attachment. No pics of houses or shaking hands, dollar bills, $, %, etc...
Please use fonts similar to Helvetica for a clean, modern look (think Northern European design, simple, clean yet bold)

Also use font colors such as blue, grey in different shades. Use pastel colors if better.

```html
<!DOCTYPE html>
<html lang="en">
<head>
<meta charset="utf-8">
<title>Velmont Realtors – Business Card</title>
<link rel="stylesheet" href="https://fonts.googleapis.com/css2?family=Cinzel:wght@400;500&family=Roboto:wght@300;400&display=swap">
<style>
  :root {
    --page: #e9e8e6;
    --card-white: #ffffff;
    --card-dark: #3a3a3b;
    --card-darker: #2b2b2c;
    --ink: #2f2f31;
    --ink-soft: #555558;
    --blue: #3f86c4;
    --blue-light: #6fb0e3;
    --silver-1: #d9d9da;
    --silver-2: #8d8d90;
    --plate-text: #f2f2f2;
  }
  * { margin: 0; padding: 0; box-sizing: border-box; }
  html, body { width: 1200px; height: 790px; overflow: hidden; }
  body {
    background: var(--page);
    font-family: "Roboto", Arial, sans-serif;
    position: relative;
  }
  .card {
    position: absolute;
    width: 520px;
    height: 297px;
    top: 246px;
    box-shadow: 0 6px 18px rgba(0,0,0,.18);
    overflow: hidden;
  }
  /* Front */
  .card-front {
    left: 50px;
    background: var(--card-white);
    display: flex;
    flex-direction: column;
    align-items: center;
    justify-content: center;
    gap: 22px;
  }
  .front-mark {
    width: 54px;
    height: 54px;
    background: linear-gradient(135deg, var(--blue-light), var(--blue));
  }
  .front-name {
    font-family: "Cinzel", Georgia, serif;
    font-size: 34px;
    font-weight: 500;
    letter-spacing: 1px;
    color: var(--ink);
  }
  /* Back */
  .card-back {
    left: 630px;
    background: var(--card-dark);
  }
  .back-topline {
    position: absolute; left: 0; top: 0; width: 100%; height: 20px;
    background: var(--card-darker);
  }
  .back-header {
    position: absolute; left: 0; top: 20px; width: 100%; height: 78px;
    background: linear-gradient(180deg, #ffffff, #ececec);
    display: flex; align-items: center; gap: 14px; padding-left: 26px;
  }
  .back-mark {
    width: 36px; height: 36px;
    background: linear-gradient(135deg, var(--blue-light), var(--blue));
  }
  .back-name {
    font-family: "Cinzel", Georgia, serif;
    font-size: 17px; font-weight: 500;
    color: var(--ink);
  }
  .contact-list {
    position: absolute; left: 282px; top: 108px; width: 238px;
    list-style: none;
    display: flex; flex-direction: column; gap: 6px;
  }
  .contact-row {
    display: flex; align-items: center;
    background: var(--card-white);
    height: 21px;
  }
  .contact-row.address { height: 40px; align-items: stretch; }
  .contact-icon {
    width: 21px; flex: none;
    background: linear-gradient(180deg, var(--blue-light), var(--blue));
    display: flex; align-items: center; justify-content: center;
  }
  .contact-icon svg { width: 12px; height: 12px; fill: none; stroke: #fff; stroke-width: 1.6; }
  .contact-text {
    font-size: 9.5px; color: var(--ink-soft);
    padding-left: 9px; line-height: 13px;
    display: flex; align-items: center;
  }
  .name-plate {
    position: absolute; left: 14px; top: 206px; width: 238px; height: 42px;
    background: linear-gradient(90deg, var(--silver-2), var(--silver-1) 55%, var(--silver-2));
    display: flex;
  }
  .name-plate-tab {
    width: 12px;
    background: linear-gradient(180deg, var(--blue-light), var(--blue));
  }
  .name-plate-text {
    padding: 7px 0 0 12px;
    color: var(--plate-text);
    text-shadow: 0 0 1px rgba(0,0,0,.3);
  }
  .person-name { font-size: 12px; letter-spacing: 1px; font-weight: 400; }
  .person-title { font-size: 9.5px; letter-spacing: .5px; font-weight: 300; margin-top: 2px; }
</style>
</head>
<body>
  <section class="card card-front">
    <div class="front-mark"></div>
    <h1 class="front-name">Velmont Realtors</h1>
  </section>

  <section class="card card-back">
    <div class="back-topline"></div>
    <header class="back-header">
      <div class="back-mark"></div>
      <h2 class="back-name">Velmont Realtors</h2>
    </header>

    <ul class="contact-list">
      <li class="contact-row">
        <span class="contact-icon"><svg viewBox="0 0 12 12"><path d="M3 1.5 L4.6 4 L3.6 5 Q4.8 7.4 7 8.4 L8 7.4 L10.5 9 L9.2 10.6 Q4.5 10 1.5 3 Z"/></svg></span>
        <span class="contact-text">012 555 0147</span>
      </li>
      <li class="contact-row">
        <span class="contact-icon"><svg viewBox="0 0 12 12"><rect x="3.5" y="1" width="5" height="10" rx="1"/><line x1="5.3" y1="9.2" x2="6.7" y2="9.2"/></svg></span>
        <span class="contact-text">012 555 0148</span>
      </li>
      <li class="contact-row">
        <span class="contact-icon"><svg viewBox="0 0 12 12"><rect x="1" y="2.5" width="10" height="7"/><path d="M1 2.5 L6 6.5 L11 2.5"/></svg></span>
        <span class="contact-text">info@velmontmail.com</span>
      </li>
      <li class="contact-row">
        <span class="contact-icon"><svg viewBox="0 0 12 12"><circle cx="6" cy="6" r="4.6"/><ellipse cx="6" cy="6" rx="2" ry="4.6"/><line x1="1.4" y1="6" x2="10.6" y2="6"/></svg></span>
        <span class="contact-text">www.velmontsite.com</span>
      </li>
      <li class="contact-row address">
        <span class="contact-icon"><svg viewBox="0 0 12 12"><path d="M6 11 Q2 6.5 2 4.5 A4 4 0 0 1 10 4.5 Q10 6.5 6 11 Z"/><circle cx="6" cy="4.6" r="1.3"/></svg></span>
        <span class="contact-text">4815 Brindle Ave. #263,<br>CA 91206</span>
      </li>
    </ul>

    <div class="name-plate">
      <div class="name-plate-tab"></div>
      <div class="name-plate-text">
        <p class="person-name">DANIEL CARVER</p>
        <p class="person-title">FINANCIAL ADVISOR</p>
      </div>
    </div>
  </section>
</body>
</html>
```